Note/Card sent to show appreciation to partners who worked with us to improve local communities

I'd like a simple note/card designed for a wide audience. Originally, I called this a "Thanksgiving Card," but it's really just a card to be sent around Thanksgiving, not specifically celebrating the Thanksgiving holiday. We plan to send the card out just prior to Thanksgiving 2017 (Nov. 24, 2017). I work at a regulated electric utility, and we'd like to say thank you to the many stakeholders who we partner with throughout the year to support initiatives that help to improve our state and create opportunities for economic growth. I'm interested mostly in the design of the card, not the simple verbiage on the inside.
Customers, charitable foundations, nonprofits, advocacy groups, industry associations, friends

```html
<!DOCTYPE html>
<html lang="en">
<head>
<meta charset="utf-8">
<title>Seasonal Appreciation Card – Two Colourways</title>
<link rel="stylesheet" href="https://fonts.googleapis.com/css2?family=Kaushan+Script&family=Great+Vibes&display=swap">
<style>
  :root {
    --canvas-bg: #ffffff;
    --card-white: #ffffff;
    --card-sage: #e9ecda;
    --card-edge: #b9b9b9;
    --wash-light: #c4dcf5;
    --wash-mid: #8cc0f7;
    --wash-deep: #5ea8f5;
    --wash-fade: rgba(170, 205, 245, 0);
    --greeting-light: #ffffff;
    --greeting-ink: #111111;
  }

  html, body {
    margin: 0;
    padding: 0;
    overflow: hidden;
  }

  body {
    width: 1200px;
    height: 1200px;
    background: var(--canvas-bg);
  }

  .presentation {
    position: relative;
    width: 1200px;
    height: 1200px;
    overflow: hidden;
  }

  .card {
    position: absolute;
    width: 450px;
    height: 450px;
    box-sizing: border-box;
    border: 1.5px solid var(--card-edge);
  }

  .card--white {
    left: 186px;
    top: 177px;
    background: var(--card-white);
  }

  .card--sage {
    left: 561px;
    top: 571px;
    background: var(--card-sage);
  }

  .card__wash {
    position: absolute;
    left: 76px;
    top: 70px;
    width: 300px;
    height: 310px;
    border-radius: 50%;
    background:
      radial-gradient(circle at 52% 46%,
        var(--wash-light) 0%,
        var(--wash-light) 38%,
        var(--wash-mid) 58%,
        var(--wash-deep) 72%,
        var(--wash-mid) 84%,
        rgba(170, 205, 245, 0.55) 94%,
        var(--wash-fade) 100%);
  }

  .card__greeting {
    position: absolute;
    left: 0;
    top: 0;
    width: 100%;
    margin: 0;
    font-weight: 400;
    text-align: center;
  }

  .card__greeting-happy {
    position: absolute;
    left: 0;
    top: 100px;
    width: 100%;
    font-family: "Kaushan Script", cursive;
    font-size: 84px;
    line-height: 1;
    color: var(--greeting-light);
    letter-spacing: 2px;
  }

  .card__greeting-occasion {
    position: absolute;
    left: 0;
    top: 206px;
    width: 100%;
    font-family: "Great Vibes", cursive;
    font-size: 80px;
    line-height: 1;
    color: var(--greeting-ink);
  }
</style>
</head>
<body>
  <main class="presentation">
    <section class="card card--white">
      <div class="card__wash" role="img" aria-label="Soft blue watercolour circle"></div>
      <h1 class="card__greeting">
        <span class="card__greeting-happy">Happy</span>
        <span class="card__greeting-occasion">Thanksgiving</span>
      </h1>
    </section>

    <section class="card card--sage">
      <div class="card__wash" role="img" aria-label="Soft blue watercolour circle"></div>
      <h1 class="card__greeting">
        <span class="card__greeting-happy">Happy</span>
        <span class="card__greeting-occasion">Thanksgiving</span>
      </h1>
    </section>
  </main>
</body>
</html>
```